Redesign of LumoWordfind.com in Bootstrap 4

Current design of LumoWordfind.com is not responsive. We need to change it to latest version of Bootstrap 4 keeping essential elements in place.

Apart from home page, we need designs for http://www.lumowordfind.com/meaning/cat also.

Coding

Number of Pages Required

2 page

Colors
34a7d8

Requirements
Must have
• Bootstrap 4

```html
<!DOCTYPE html>
<html lang="en">
<head>
<meta charset="utf-8">
<title>Lumo Wordfind – English Dictionary</title>
<link href="https://fonts.googleapis.com/css2?family=Roboto:wght@400;500&family=Open+Sans:wght@400;600&family=Oswald:wght@400&display=swap" rel="stylesheet">
<style>
:root{
  --blue:#1d6fa8;
  --blue-light:#34a7d8;
  --hero-dark:#0d3553;
  --hero-mid:#1c5f8c;
  --orange:#f7960f;
  --ink:#333;
  --muted:#555;
  --border:#d9d9d9;
  --footer:#2c2c2c;
  --footer-text:#9a9a9a;
}
*{box-sizing:border-box;margin:0;padding:0}
html,body{width:796px;height:1200px;overflow:hidden}
body{position:relative;background:#fff;font-family:"Open Sans",sans-serif;color:var(--ink)}
.abs{position:absolute}

/* header */
.site-header{left:0;top:0;width:796px;height:84px;border-top:2px solid var(--blue)}
.brand{left:64px;top:22px;font-family:"Roboto",sans-serif;font-weight:500;font-size:19px;color:var(--blue);display:flex;align-items:center;gap:6px;line-height:1}
.brand-dot{width:12px;height:12px;background:var(--orange);border-radius:50%}
.login-field{top:20px;width:96px;height:21px;border:1px solid #ddd;font-family:"Roboto",sans-serif;font-size:8px;color:#aaa;padding:6px 7px}
.login-btn{left:674px;top:20px;width:56px;height:21px;background:var(--blue);color:#fff;font-family:"Roboto",sans-serif;font-size:9.5px;text-align:center;line-height:21px}
.main-nav{top:53px;font-family:"Roboto",sans-serif;font-weight:500;font-size:9.5px;color:#444}
.main-nav.active{color:var(--blue)}

/* hero */
.hero{left:0;top:84px;width:796px;height:282px;background:radial-gradient(ellipse at 50% 30%,var(--hero-mid),var(--hero-dark) 85%);color:#fff;text-align:center}
.hero-title{position:absolute;left:0;width:100%;top:52px;font-family:"Oswald",sans-serif;font-weight:400;font-size:36px;line-height:1.2}
.hero-lead{position:absolute;left:118px;width:560px;top:107px;font-family:"Roboto",sans-serif;font-size:14.5px;line-height:21px}
.search{position:absolute;left:146px;top:172px;width:503px;height:37px;display:flex;box-shadow:0 0 0 2px rgba(255,255,255,.15)}
.search-input{flex:1;background:#fff;color:#777;font-family:"Roboto",sans-serif;font-size:11px;text-align:left;padding:11px 12px}
.search-btn{width:89px;background:var(--orange);font-family:"Roboto",sans-serif;font-weight:500;font-size:12px;line-height:37px}
.search-hint{position:absolute;left:146px;top:222px;font-family:"Roboto",sans-serif;font-size:9px}

/* feature cards */
.card{left:65px;width:445px;height:122px;border:1px solid var(--border)}
.card-media{position:absolute;left:12px;top:13px;width:153px;height:96px}
.card-body{position:absolute;left:180px;top:11px;width:252px;height:100px}
.card-title{font-family:"Roboto",sans-serif;font-weight:400;font-size:11.5px;color:#222;margin-bottom:12px}
.card-sub{font-size:7.5px;margin-bottom:6px}
.card-text{font-size:7.5px;line-height:12.5px;color:var(--muted);text-align:justify}
.btn-orange{display:inline-block;background:var(--orange);color:#fff;font-size:7.5px;font-weight:600;padding:0 10px;height:21px;line-height:21px}
.card-body .btn-orange{position:absolute;top:76px;left:0}

/* sidebar */
.word-day{left:536px;top:398px;width:194px;height:140px;background:var(--blue);border:2px solid #2a80bd;color:#fff}
.word-day h3{position:absolute;left:14px;top:10px;font-family:"Oswald",sans-serif;font-weight:400;font-size:14px}
.word-box{position:absolute;left:14px;top:38px;width:164px;height:48px;background:#fff;color:#333;padding:7px 8px;font-family:"Roboto",sans-serif}
.word-box b{font-weight:400;font-size:10.5px;display:block}
.word-box span{font-size:7.5px}
.share{position:absolute;left:16px;top:104px;display:flex;gap:7px}
.share i{width:9px;height:9px;border-radius:50%;background:#fff;display:block}
.word-day .btn-orange{position:absolute;left:93px;top:98px;font-family:"Roboto",sans-serif;font-size:8.5px;font-weight:400;height:23px;line-height:23px;padding:0 10px}
.perks{left:536px;top:555px;width:194px;height:227px;border:1px solid var(--border);padding:13px 10px}
.perks h3{font-family:"Roboto",sans-serif;font-weight:400;font-size:11.5px;line-height:17px;color:#222;margin-bottom:10px}
.perks li{list-style:none;position:relative;padding-left:13px;font-size:7.8px;line-height:20px;color:var(--muted);text-align:justify}
.perks li svg{position:absolute;left:0;top:6px}

/* pagination */
.browse{left:65px;top:968px;display:flex;align-items:center;gap:6px;font-family:"Roboto",sans-serif;font-size:8.5px;color:#444}
.browse .label{margin-right:10px}
.page{height:17px;min-width:17px;padding:0 4px;border:1px solid #ccc;box-shadow:0 1px 1px #ddd;font-size:7px;text-align:center;line-height:15px;color:#333}
.page.wide{padding:0 8px;font-weight:500}

/* footer */
.site-footer{left:0;top:1008px;width:796px;height:192px;background:var(--footer);font-family:"Roboto",sans-serif}
.foot-col{position:absolute;top:30px}
.foot-col h4{font-weight:500;font-size:10px;color:#fff;margin-bottom:17px}
.foot-col p{font-size:8.5px;color:var(--footer-text);line-height:17.6px}
.newsletter p{width:160px;line-height:14px}
.email{width:150px;height:27px;background:#fff;color:#aaa;font-size:6.5px;padding:10px 8px;margin-top:14px}
.subscribe{width:72px;height:27px;background:var(--blue);color:#fff;font-size:9px;font-weight:500;line-height:27px;text-align:center;margin-top:6px}
.copyright{position:absolute;left:66px;top:153px;font-size:9px;color:var(--footer-text)}
</style>
</head>
<body>

<header class="abs site-header">
  <div class="abs brand"><span class="brand-dot"></span>Lumo Wordfind</div>
  <div class="abs login-field" style="left:468px">User Name</div>
  <div class="abs login-field" style="left:570px">Password</div>
  <div class="abs login-btn">LOGIN</div>
  <span class="abs main-nav active" style="left:351px">HOME</span>
  <span class="abs main-nav" style="left:402px">IDIOMS</span>
  <span class="abs main-nav" style="left:458px">COMMON ERRORS</span>
  <span class="abs main-nav" style="left:561px">CROSSWORD</span>
  <span class="abs main-nav" style="left:642px">BLOG</span>
  <span class="abs main-nav" style="left:690px">CONTACT</span>
</header>

<section class="abs hero">
  <h1 class="hero-title">Lumo English Dictionary</h1>
  <p class="hero-lead">Lorem ipsum dolor sit amet, consectetur adipiscing elit, sed do eiusmod tempor ut labore et dolore magna aliqua ut enim ad minim veniam.</p>
  <div class="search">
    <div class="search-input">Enter a word or Phrase</div>
    <div class="search-btn">SEARCH</div>
  </div>
  <p class="search-hint">(e.g) Fire,Beauty,Quote</p>
</section>

<article class="abs card" style="top:398px">
  <div class="card-media" role="img" aria-label="Businessman writing the word English" style="background:linear-gradient(120deg,#e9e9e9,#a8a8a8 60%,#6e6e6e)"></div>
  <div class="card-body">
    <h2 class="card-title">ENGLISH TIDBIT</h2>
    <p class="card-sub">Gaffe / Gaff</p>
    <p class="card-text">"Gaffe" is a social blunder and "gaff" is a large hook. Be warned not to make the gaffe of mixing it up with gaff.</p>
    <span class="btn-orange">READ MORE</span>
  </div>
</article>

<article class="abs card" style="top:539px">
  <div class="card-media" role="img" aria-label="Hand filling in a crossword puzzle" style="background:linear-gradient(135deg,#f2dcc8,#c9c3bd 45%,#6b6b6b)"></div>
  <div class="card-body">
    <h2 class="card-title">DAILY CROSSWORD</h2>
    <p class="card-sub">Crossword Lovers!</p>
    <p class="card-text">Take this daily crossword challenge from Lumo Wordfind.Take this daily crossword challenge from Lumo Wordfind.</p>
    <span class="btn-orange">SOLVE NOW</span>
  </div>
</article>

<article class="abs card" style="top:682px">
  <div class="card-media" role="img" aria-label="Browser window screenshot" style="background:linear-gradient(160deg,#2b5fa8,#dfe8f2 35%,#f4f6f8)"></div>
  <div class="card-body">
    <h2 class="card-title">FOXTRAIL ADDON</h2>
    <p class="card-sub">Crossword Lovers!</p>
    <p class="card-text">Add this tool to your Foxtrail browser and quickly look up for definitions from any website without leaving the page.</p>
    <span class="btn-orange">GET IT NOW</span>
  </div>
</article>

<article class="abs card" style="top:825px">
  <div class="card-media" role="img" aria-label="Tablet beside a stack of books" style="background:linear-gradient(110deg,#f1f1f1,#9a8c7c 55%,#4f6d78)"></div>
  <div class="card-body">
    <h2 class="card-title">DESIGNED FOR POCKETPHONE</h2>
    <p class="card-sub">Crossword Lovers!</p>
    <p class="card-text">Lumo Wordfind is specially designed for your Pocketphone to quickly lookup meaining, usages and audio of words.</p>
    <span class="btn-orange">READ MORE</span>
  </div>
</article>

<aside class="abs word-day">
  <h3>Word of the Day</h3>
  <div class="word-box"><b>Exhaustive</b><span>/ig zc strv /</span></div>
  <div class="share"><i></i><i></i><i></i></div>
  <span class="btn-orange">Show Definition</span>
</aside>

<aside class="abs perks">
  <h3>SEARCH, SAVE AND MASTER WORDS</h3>
  <ul>
    <li><svg width="8" height="7" viewBox="0 0 8 7"><path d="M1 3.5l2 2L7 1" stroke="#f7960f" stroke-width="1.6" fill="none"/></svg>Search from more than 300,000 words and phrases</li>
    <li><svg width="8" height="7" viewBox="0 0 8 7"><path d="M1 3.5l2 2L7 1" stroke="#f7960f" stroke-width="1.6" fill="none"/></svg>Multiple usages to clarify the context</li>
    <li><svg width="8" height="7" viewBox="0 0 8 7"><path d="M1 3.5l2 2L7 1" stroke="#f7960f" stroke-width="1.6" fill="none"/></svg>Audio, phonetics, meanings, synonyms and antonyms</li>
    <li><svg width="8" height="7" viewBox="0 0 8 7"><path d="M1 3.5l2 2L7 1" stroke="#f7960f" stroke-width="1.6" fill="none"/></svg>Save the words to your personal deck and access from anywhere</li>
    <li><svg width="8" height="7" viewBox="0 0 8 7"><path d="M1 3.5l2 2L7 1" stroke="#f7960f" stroke-width="1.6" fill="none"/></svg>It's FREE</li>
  </ul>
</aside>

<nav class="abs browse">
  <span class="label">Browse Dictionary</span>
  <span class="page wide" style="margin-right:4px">Prev</span>
  <span class="page">A</span><span class="page">B</span><span class="page">C</span><span class="page">D</span><span class="page">E</span><span class="page">F</span><span class="page">...</span><span class="page">P</span>
  <span class="page wide">Next</span>
</nav>

<footer class="abs site-footer">
  <div class="foot-col" style="left:66px"><h4>LUMO WORDFIND</h4><p>Meaning/Definition</p><p>Audio</p><p>Phonetics</p><p>Usages</p></div>
  <div class="foot-col" style="left:199px"><h4>INFORMATION</h4><p>FAQ</p><p>Contact</p><p>Blog</p></div>
  <div class="foot-col" style="left:329px"><h4>LEGAL</h4><p>Privacy Policy</p><p>Terms of Use</p></div>
  <div class="foot-col" style="left:433px"><h4>OTHERS</h4><p>Popular Words</p><p>Common Errors in English</p><p>Diploma Prep Online</p></div>
  <div class="foot-col newsletter" style="left:579px"><h4>NEWSLETTER SIGN UP</h4><p>Lorem ipsum dolor sit amet, consectetur adipiscing elit eiusmod tempor</p><div class="email">Email Address....</div><div class="subscribe">SUBSCRIBE</div></div>
  <p class="copyright">Copyright © 2016 Lumo Wordfind.All rights reserved.</p>
</footer>

</body>
</html>
```